Volbrey Inc Business Card

Looking to get an updated business card for a Contract Machining company (www.volbreyinc.example) - looking for a clean design the portrays the technical nature of the business - colors can follow the website design and be in any combination that makes sense (red black, white, metallic or silver) - logos attached for use also. Would like space for: Name, title, business phone (555 214-3086), cell phone , website (www.volbreyinc.example) - possibly QR code could be integrated for website (designer choice), business address - 418 Harlow Bend, Ashvale, OH 44199 (cards will be for 4 employees, I will either need to modify a template or I can provide individual information)
Target Market(s)
Aerospace, defense and medical device manufacturing companies that need machining
Industry/Entity Type
Machining for aerospace, defense, medical
Contact Information for Business Card
Name, Title, Business Phone, Cell Phone, email, business website and business address
Look and feel

```html
<!DOCTYPE html>
<html lang="en">
<head>
<meta charset="utf-8">
<title>Volbrey Inc Business Card</title>
<link rel="stylesheet" href="https://fonts.googleapis.com/css2?family=Montserrat:wght@400;500;600&display=swap">
<style>
  :root {
    --backdrop: #e6e4e5;
    --card-white: #ffffff;
    --brand-red: #b11f24;
    --ink: #1c1c1c;
    --card-black: #111111;
  }
  * { margin: 0; padding: 0; box-sizing: border-box; }
  html, body {
    width: 1200px;
    height: 1108px;
    overflow: hidden;
    background: var(--backdrop);
    font-family: "Montserrat", sans-serif;
    color: var(--ink);
  }
  .canvas { position: relative; width: 1200px; height: 1108px; }

  .card { position: absolute; left: 228px; width: 756px; }
  .card-front { top: 56px; height: 461px; background: var(--card-white); }
  .card-back { top: 575px; height: 444px; background: var(--card-black); overflow: hidden; }

  .brand-mark {
    position: absolute; left: 220px; top: 173px;
    width: 128px; height: 128px; border-radius: 50%;
    background: var(--brand-red);
  }
  .brand-name {
    position: absolute; left: 184px; top: 310px; width: 200px;
    text-align: center; font-weight: 600; font-size: 19px;
    letter-spacing: 0.5px; color: var(--brand-red);
  }

  .divider {
    position: absolute; left: 376px; top: 170px;
    width: 2px; height: 168px; background: var(--brand-red);
  }

  .person { position: absolute; left: 397px; top: 168px; }
  .person-name { font-weight: 600; font-size: 29px; color: var(--brand-red); line-height: 1.1; }
  .person-title { font-weight: 400; font-size: 17px; margin-top: 2px; padding-left: 2px; }

  .contact-list { position: absolute; left: 403px; top: 240px; list-style: none; }
  .contact-item {
    display: flex; align-items: center; gap: 8px;
    font-size: 17px; line-height: 24px; height: 24.5px;
  }
  .contact-icon { width: 15px; height: 15px; flex: none; fill: var(--brand-red); }

  .address {
    position: absolute; left: 0; right: 0; top: 387px;
    text-align: center; font-size: 17px; padding-right: 10px;
  }

  .back-pattern {
    position: absolute; inset: 0;
    background: radial-gradient(ellipse at 8% 10%, #5a5a5a 0%, #2a2a2a 30%, var(--card-black) 60%);
  }
</style>
</head>
<body>
<main class="canvas">
  <section class="card card-front" aria-label="Business card front">
    <div class="brand-mark" aria-hidden="true"></div>
    <p class="brand-name">VOLBREY INC</p>
    <div class="divider"></div>
    <div class="person">
      <h1 class="person-name">Daniel Moreau</h1>
      <p class="person-title">Owner</p>
    </div>
    <ul class="contact-list">
      <li class="contact-item">
        <svg class="contact-icon" viewBox="0 0 16 16" aria-hidden="true"><path d="M3.5 1l2.5 3-1.5 2c1 2 3 4 5 5l2-1.5 3 2.5-1.5 2.5C7 15 1 9 1 2.5z"/></svg>
        <span>555 214-3086</span>
      </li>
      <li class="contact-item">
        <svg class="contact-icon" viewBox="0 0 16 16" aria-hidden="true"><path d="M1 5c0-2 14-2 14 0v1.5h-3.5V5h-7v1.5H1zM3 7.5h10l1.5 6.5h-13z"/></svg>
        <span>555 214-3086</span>
      </li>
      <li class="contact-item">
        <svg class="contact-icon" viewBox="0 0 16 16" aria-hidden="true"><path d="M1 3h14v1.5L8 9 1 4.5zM1 6l7 4.5L15 6v7H1z"/></svg>
        <span>info@volbreyinc.example</span>
      </li>
      <li class="contact-item">
        <svg class="contact-icon" viewBox="0 0 16 16" aria-hidden="true"><circle cx="8" cy="8" r="7"/><path d="M4 4c2 0 3 2 2 3s-2 2 0 4l-1 3M10 2c-1 2 1 3 3 3M11 9c1 1 0 3-1 4" stroke="#fff" stroke-width="1.2" fill="none"/></svg>
        <span>www.volbreyinc.example</span>
      </li>
    </ul>
    <p class="address">418 Harlow Bend, Ashvale, OH 44199</p>
  </section>

  <section class="card card-back" aria-label="Business card back">
    <div class="back-pattern" role="img" aria-label="Repeating brand emblem pattern on black with one red emblem accent"></div>
  </section>
</main>
</body>
</html>
```